We are building a website where users come to see what skills they will need for their career. The content of the page is data-driven, so the site should have the feel of a set of data dashboards. The data is collected and processed using machine learning. The main idea is for the user to come in and spend some minutes exploring, scrolling and clicking around.
The task is to design a website with four pages:
Front page
Early career page
Skill trends page
Skills Page
Each of these is described in attached files, along with example data
We need the resulting files to be exported also to uncompressed PNG, and in the case of vector graphics, to SVG.
Target Market(s)
People Looking to start a Career and Policy makers.
Industry/Entity Type
Human Resource
Number of Pages Required
4 page
Look and feel

```html
<!DOCTYPE html>
<html lang="en">
<head>
<meta charset="utf-8">
<title>Talentora – Page Designs</title>
<link rel="stylesheet" href="https://fonts.googleapis.com/css2?family=Cinzel:wght@400;500;600&family=Roboto:wght@400;500;700&display=swap">
<style>
:root{
  --navy:#0f0a5c;
  --indigo:#2d2a90;
  --magenta:#9b1a80;
  --pink:#e04bbf;
  --teal:#2a9d78;
  --sky:#3f8fbf;
  --lav:#f6f4fb;
  --row:#ebe9fa;
  --track:#e2ddf1;
  --gtrack:#d3d3d8;
  --ink:#2a2a33;
  --muted:#8a8a96;
  --board:#9a9a9a;
  --footer:#1c1b1f;
  --white:#ffffff;
}
*{box-sizing:border-box;margin:0;padding:0}
html,body{width:1200px;height:2265px;overflow:hidden;background:var(--board);font-family:Roboto,Arial,sans-serif;color:var(--ink)}
.board{position:absolute;left:0;top:0;width:1365px;height:2576px;transform:scale(0.879121);transform-origin:0 0}
.board-shapes{position:absolute;inset:0}
.page{position:absolute;width:546px;background:var(--white);overflow:hidden}
.page-career{left:120px;top:65px;height:1395px}
.page-skills{left:699px;top:65px;height:1162px}
.page-trends{left:120px;top:1495px;height:1015px}
.abs{position:absolute}

/* hero */
.hero{position:absolute;left:0;top:0;width:546px;height:194px;overflow:hidden}
.hero-bg{position:absolute;inset:0}
.brand{position:absolute;left:65px;top:16px;font:500 17px/1 Roboto,sans-serif;color:var(--white);letter-spacing:.6px}
.nav{position:absolute;left:239px;top:17px;display:flex;align-items:center;gap:16px;font:700 5.6px/1 Roboto,sans-serif;color:var(--white);letter-spacing:.2px}
.nav span{padding:2px 0}
.nav .active{border-bottom:1px solid var(--white)}
.nav .login{background:var(--magenta);border-radius:10px;padding:6px 15px;font-size:6px}
.hero-title{position:absolute;left:0;top:92px;width:100%;text-align:center;font:500 35px/1 Cinzel,serif;color:var(--white);letter-spacing:.8px}
.crumbs{position:absolute;left:0;top:139px;width:100%;text-align:center;font:400 5.6px/1 Roboto,sans-serif;color:var(--white)}
.crumbs em{font-style:normal;color:var(--pink)}

/* banner */
.banner{position:absolute;left:93px;top:210px;width:360px;height:100px;border-radius:6px;overflow:hidden;background:#e3e3e8}
.banner-photo{position:absolute;left:0;top:0;height:100%}
.banner-tag{position:absolute;top:18px;width:120px;height:64px;background:var(--magenta);border-radius:5px;color:var(--white);display:flex;flex-direction:column;justify-content:center;padding-left:17px}
.banner-tag .tag-label{font:500 12.5px/1.35 Roboto,sans-serif}
.banner-tag .tag-value{font:400 12.5px/1.35 Roboto,sans-serif}
.banner-tag.large{align-items:center;padding-left:0;text-align:center;font:500 17.5px/1.15 Roboto,sans-serif}

/* headings */
.sec-title{position:absolute;font:500 15.5px/20px Cinzel,serif;color:var(--navy);letter-spacing:.4px}
.sec-title.small{font-size:12.5px;line-height:15.5px}
.accent{color:var(--magenta)}
.center{left:0;width:100%;text-align:center}

/* tables */
.data-table{position:absolute;border-collapse:collapse;table-layout:fixed;font:400 5.4px/1 Roboto,sans-serif;color:var(--ink)}
.data-table th{background:var(--navy);color:var(--white);font-weight:700;height:14px;text-align:center;border-right:1px solid #fff}
.data-table td{height:20px;padding:0 6px;border-right:1px solid #dcdcea;border-bottom:1px solid #dcdcea;white-space:nowrap;overflow:hidden}
.data-table tr:nth-child(odd) td{background:var(--row)}
.data-table.compact th{height:12px}
.data-table.compact td{height:18.8px;text-align:center}
.data-table.mini{font-size:4.2px}
.data-table.mini th{height:11px}
.data-table.mini td{height:12px;padding:0 4px;text-align:left}
.data-table.mini td.score{text-align:right}
.meter-cell{display:flex;align-items:center;justify-content:space-between;gap:6px;padding:0 10px 0 20px}
.meter{flex:none;width:70px;height:3px;background:var(--track);border-radius:2px;overflow:hidden}
.meter i{display:block;height:100%;background:var(--magenta);border-radius:2px}
.task-meter{display:flex;flex-direction:column;align-items:flex-end;gap:3px;padding:0 8px}
.task-meter .meter{width:64px;align-self:flex-start}

.panel{position:absolute;background:var(--lav)}
svg text{font-family:Roboto,sans-serif}

/* modifiers */
.mod-head{position:absolute;font:500 10px/1 Roboto,sans-serif;color:var(--magenta)}
.mod{position:absolute;width:183px}
.mod-label{display:flex;justify-content:space-between;padding-right:30px;font:500 5.2px/1 Roboto,sans-serif;color:var(--ink)}
.mod-bar{margin-top:8px;height:7px;background:var(--gtrack);border-radius:4px;overflow:hidden}
.mod-bar i{display:block;width:54%;height:100%;background:var(--navy);border-radius:4px}
.link{position:absolute;left:66px;font:500 7px/1 Roboto,sans-serif;color:var(--navy)}

/* lexical */
.syn-list{position:absolute;left:66px;top:1040px;list-style:none;font:400 7px/14px Roboto,sans-serif;color:var(--ink)}
.syn-list li{display:flex;align-items:center;gap:7px}
.tick{width:7px;height:7px;border-radius:50%;background:var(--magenta);display:inline-flex;align-items:center;justify-content:center}
.quote-banner{position:absolute;left:231px;top:1014px;width:249px;height:71px;border-radius:3px;overflow:hidden}
.quote-strip{position:absolute;left:35px;top:21px;width:179px;height:30px;background:rgba(155,26,128,.85);color:var(--white);font:700 8px/10px Roboto,sans-serif;text-align:center;display:flex;align-items:center;justify-content:center}

/* categories */
.cat{position:absolute;top:399px;width:90px;margin-left:-45px;text-align:center}
.cat-ring{width:68px;height:68px;margin:0 auto;border:2px solid var(--magenta);border-radius:50%;display:flex;align-items:center;justify-content:center;background:var(--white)}
.cat-ring.active{border-width:4px}
.cat-name{margin-top:10px;font:500 6.2px/7px Roboto,sans-serif;color:var(--ink)}
.cat-sub{margin-top:5px;font:400 5.2px/10px Roboto,sans-serif;color:var(--muted)}

/* footer */
.footer{position:absolute;left:0;bottom:0;width:546px;height:50px;background:var(--footer);color:var(--white)}
.mail{position:absolute;left:65px;top:14px;display:flex;align-items:center;gap:6px;font:500 8px/1 Roboto,sans-serif}
.mail-icon{width:22px;height:22px;border:1.5px solid var(--white);border-radius:50%;display:flex;align-items:center;justify-content:center}
.legal{position:absolute;left:218px;top:23px;font:400 5.2px/1 Roboto,sans-serif}
.social{position:absolute;top:14px;width:22px;height:22px;border-radius:50%;background:var(--white)}
</style>
</head>
<body>
<div class="board">
  <svg class="board-shapes" width="1365" height="2576" viewBox="0 0 1365 2576" aria-hidden="true">
    <path d="M40 0 Q62 95 120 130 L120 212 L1365 212 L1365 0 Z" fill="var(--magenta)"/>
    <path d="M0 2190 L1010 2190 Q1290 2240 1365 2470 L1365 2576 L0 2576 Z" fill="var(--magenta)"/>
  </svg>

  <!-- EARLY CAREER -->
  <section class="page page-career">
    <header class="hero">
      <div class="hero-bg" role="img" aria-label="Photo of a professional in a suit under a blue colour overlay" style="background:linear-gradient(100deg,#1f17cf 0%,#1a14b0 55%,#120c70 78%,#0c0a4a 100%)"></div>
      <div class="brand">Talentora</div>
      <nav class="nav"><span>HOME</span><span class="active">EARLY CAREER</span><span>SKILL TRENDS</span><span>SKILLS</span><span class="login">LOGIN</span></nav>
      <h1 class="hero-title">EARLY CAREER</h1>
      <div class="crumbs">Home / Skill / <em>Occupation</em> / Category</div>
    </header>

    <div class="banner">
      <div class="banner-photo" role="img" aria-label="Photo of a developer working at several screens of code" style="width:260px;background:linear-gradient(90deg,#4a4c5a 0%,#22242e 45%,#3b3e4c 75%,#c9cad2 100%)"></div>
      <div class="banner-tag" style="left:225px"><span class="tag-label">Occupation</span><span class="tag-value">Web developer</span></div>
    </div>

    <h2 class="sec-title center" style="top:345px">SKILLS THAT THE MARKET REQUIRES<br><span class="accent">FOR THIS OCCUPATION</span></h2>

    <table class="data-table" style="left:65px;top:406px;width:415px">
      <thead><tr><th style="width:66px">SKILL</th><th style="width:76px">SUBSKILLS</th><th style="width:137px">% OF JOB ADS THAT MENTION IT</th><th>APPEAR AS MANDATORY</th></tr></thead>
      <tbody>
        <tr><td>Kava Programming</td><td>Leafboot, Dormant</td><td><div class="meter-cell"><span class="meter"><i style="width:30%"></i></span><span>30%</span></div></td><td><div class="meter-cell"><span class="meter"><i style="width:50%"></i></span><span>50%</span></div></td></tr>
        <tr><td>Serpa Programming</td><td>Vial,QuickAPI</td><td><div class="meter-cell"><span class="meter"><i style="width:40%"></i></span><span>40%</span></div></td><td><div class="meter-cell"><span class="meter"><i style="width:85%"></i></span><span>70%</span></div></td></tr>
        <tr><td>Webscript</td><td>Reflex, Nodus</td><td><div class="meter-cell"><span class="meter"><i style="width:75%"></i></span><span>60%</span></div></td><td><div class="meter-cell"><span class="meter"><i style="width:90%"></i></span><span>80%</span></div></td></tr>
        <tr><td>Kava Programming</td><td></td><td><div class="meter-cell"><span class="meter"><i style="width:50%"></i></span><span>50%</span></div></td><td><div class="meter-cell"><span class="meter"><i style="width:15%"></i></span><span>15%</span></div></td></tr>
        <tr><td>Kava Programming</td><td>Paired Programming</td><td><div class="meter-cell"><span class="meter"><i style="width:30%"></i></span><span>30%</span></div></td><td><div class="meter-cell"><span class="meter"><i style="width:5%"></i></span><span>5%</span></div></td></tr>
      </tbody>
    </table>

    <h3 class="sec-title small" style="left:88px;top:572px">LIST OF EDUCATIONAL<br>REQUIREMENTS <span class="accent">MENTIONED</span><br><span class="accent">FOR THIS OCCUPATION</span></h3>
    <h3 class="sec-title small" style="left:311px;top:572px">OTHER CERTIFICATES<br><span class="accent">THAT COULD BE OF</span><br>BENEFIT</h3>

    <svg class="abs" style="left:0;top:625px" width="546" height="160" viewBox="0 625 546 160" role="img" aria-label="Pie charts of education requirements and other certificates">
      <path d="M161 705 L88 705 A73 73 0 0 1 183.6 635.6 Z" fill="var(--magenta)"/>
      <path d="M161 705 L183.6 635.6 A73 73 0 0 1 234 705 Z" fill="var(--indigo)"/>
      <path d="M161 705 L234 705 A73 73 0 0 1 88 705 Z" fill="var(--navy)"/>
      <g fill="#fff" font-size="7.5" text-anchor="middle">
        <text x="139" y="680">Technical degree</text><text x="139" y="691">30%</text>
        <text x="207" y="679">No Degree</text><text x="207" y="690">Mentioned</text><text x="207" y="701">20%</text>
        <text x="158" y="736">Master's Degree</text><text x="158" y="747">50%</text>
      </g>
      <path d="M385 705 L312 705 A73 73 0 0 1 362.4 635.6 Z" fill="var(--indigo)"/>
      <path d="M385 705 L362.4 635.6 A73 73 0 0 1 458 705 Z" fill="var(--teal)"/>
      <path d="M385 705 L458 705 A73 73 0 0 1 385 778 Z" fill="var(--magenta)"/>
      <path d="M385 705 L385 778 A73 73 0 0 1 312 705 Z" fill="#f4e8ec"/>
      <g fill="#fff" font-size="7.5" text-anchor="middle">
        <text x="349" y="678">Kernix Engineer</text><text x="349" y="689">Certification</text><text x="349" y="700">20%</text>
        <text x="416" y="678">Kava Certified</text><text x="416" y="689">Engineer</text><text x="416" y="700">30%</text>
        <text x="412" y="736">Cloud Computing</text><text x="412" y="747">Certification</text><text x="412" y="758">25%</text>
      </g>
    </svg>

    <div class="panel" style="left:65px;top:812px;width:415px;height:286px"></div>
    <h2 class="sec-title center" style="top:838px">AMOUNT OF EXPERIENCE USUALLY<br>REQUIRED : <span class="accent">NUMBER OF YEARS</span></h2>
    <svg class="abs" style="left:0;top:885px" width="546" height="190" viewBox="0 885 546 190" role="img" aria-label="Bar chart of years of experience required">
      <line x1="201" y1="893" x2="201" y2="1046" stroke="#c9c7d6" stroke-width=".8"/>
      <line x1="201" y1="1046" x2="387" y2="1046" stroke="#c9c7d6" stroke-width=".8"/>
      <g font-size="5" fill="#333" text-anchor="end">
        <text x="188" y="921">60</text><text x="188" y="946">50</text><text x="188" y="971">40</text><text x="188" y="996">30</text><text x="188" y="1021">20</text><text x="188" y="1046">10</text>
      </g>
      <text transform="translate(166 970) rotate(-90)" font-size="7" fill="#333" text-anchor="middle">Percentage</text>
      <rect x="213" y="1024" width="25" height="22" fill="var(--navy)"/>
      <rect x="248" y="922" width="25" height="124" fill="var(--magenta)"/>
      <rect x="283" y="1009" width="25" height="37" fill="var(--navy)"/>
      <rect x="319" y="1024" width="25" height="22" fill="var(--magenta)"/>
      <g font-size="7" fill="#333" text-anchor="middle">
        <text x="225" y="1018">10%</text><text x="260" y="917">52%</text><text x="296" y="1004">23%</text><text x="332" y="1020">15%</text>
      </g>
      <g font-size="4.6" fill="#333" text-anchor="middle">
        <text x="202" y="1062">0</text><text x="218" y="1062">0-2</text><text x="244" y="1062">3-5</text><text x="269" y="1062">5-7</text><text x="296" y="1062">7+</text>
      </g>
      <text x="336" y="1069" font-size="7" fill="#333">Years required</text>
    </svg>

    <h3 class="sec-title small" style="left:65px;top:1138px">TASKS USUALLY ASSOCIATED<br><span class="accent">WITH THIS OCCUPATION</span></h3>
    <h3 class="sec-title small" style="left:285px;top:1138px">LIST OF RAPID INCREASING<br><span class="accent">SKILLS</span></h3>

    <table class="data-table compact" style="left:65px;top:1188px;width:195px">
      <thead><tr><th style="width:115px">TASK</th><th>PERCENTAGE</th></tr></thead>
      <tbody>
        <tr><td>Developing Unit Tests</td><td><div class="task-meter"><span>30%</span><span class="meter"><i style="width:30%"></i></span></div></td></tr>
        <tr><td>Writing Documentation</td><td><div class="task-meter"><span>10%</span><span class="meter"><i style="width:12%"></i></span></div></td></tr>
        <tr><td>Writing Documentation</td><td><div class="task-meter"><span>15%</span><span class="meter"><i style="width:15%"></i></span></div></td></tr>
        <tr><td>Writing code</td><td><div class="task-meter"><span>50%</span><span class="meter"><i style="width:60%"></i></span></div></td></tr>
        <tr><td>Mentoring</td><td><div class="task-meter"><span>30%</span><span class="meter"><i style="width:45%"></i></span></div></td></tr>
        <tr><td>Code Review</td><td><div class="task-meter"><span>20%</span><span class="meter"><i style="width:15%"></i></span></div></td></tr>
      </tbody>
    </table>

    <table class="data-table compact" style="left:285px;top:1188px;width:195px">
      <thead><tr><th style="width:112px">SKILL</th><th>INCREASING</th></tr></thead>
      <tbody>
        <tr><td>BYTEASM</td><td>Slowly</td></tr>
        <tr><td>WebPix</td><td>Fast</td></tr>
        <tr><td>Bootframe5</td><td>Slowly</td></tr>
        <tr><td>RepoOps</td><td>Fast</td></tr>
      </tbody>
    </table>

    <footer class="footer">
      <div class="mail"><span class="mail-icon"><svg width="11" height="8" viewBox="0 0 11 8"><rect x=".5" y=".5" width="10" height="7" rx="1" fill="#fff"/><path d="M1 1 L5.5 4.5 L10 1" stroke="#1c1b1f" fill="none"/></svg></span>Email : info@talentora.example</div>
      <div class="legal">© 2021 Talentora. All rights reserved &nbsp;| Privacy Policy &nbsp;| &nbsp;Terms of Use</div>
      <span class="social" style="left:429px"></span><span class="social" style="left:457px"></span>
    </footer>
  </section>

  <!-- SKILLS -->
  <section class="page page-skills">
    <header class="hero">
      <div class="hero-bg" role="img" aria-label="Abstract blue technology artwork with gears and glowing network points" style="background:radial-gradient(circle at 28% 70%,#2a5cff 0%,#1a22d8 30%,#10108a 62%,#0c0a52 100%)"></div>
      <div class="brand">Talentora</div>
      <nav class="nav"><span>HOME</span><span>EARLY CAREER</span><span>SKILL TRENDS</span><span class="active">SKILLS</span><span class="login">LOGIN</span></nav>
      <h1 class="hero-title">SKILLS</h1>
      <div class="crumbs">Home / <em>Skill</em> / Occupation / Category</div>
    </header>

    <div class="banner" style="background:#eceef2">
      <div class="banner-photo" role="img" aria-label="Photo of a designer's desk with sketches and people working at a monitor" style="width:360px;background:linear-gradient(90deg,#d9d6cf 0%,#b9b4aa 25%,#e8e9ee 55%,#c7cbd6 80%,#eef0f4 100%)"></div>
      <div class="banner-tag large" style="left:83px">Graphic<br>Design</div>
    </div>

    <div class="link" style="top:341px">http://data.skillatlas.example/skill/7fb699d9-182a-430e-b7a0-6d8ed05c284b</div>
    <h2 class="sec-title" style="left:66px;top:356px">SKILL <span class="accent">DETAILS</span></h2>
    <div class="link" style="top:383px">https://wiki.skillatlas.example/Graphic_design</div>

    <h2 class="sec-title" style="left:66px;top:418px">MODIFIERS</h2>
    <div class="mod-head" style="left:65px;top:452px">Education</div>
    <div class="mod-head" style="left:296px;top:452px">Level of mastery</div>
    <div class="mod" style="left:66px;top:479px"><div class="mod-label"><span>University degree</span><span>50%</span></div><div class="mod-bar"><i></i></div></div>
    <div class="mod" style="left:66px;top:515px"><div class="mod-label"><span>Vectorpro certificate</span><span>30%</span></div><div class="mod-bar"><i></i></div></div>
    <div class="mod" style="left:66px;top:552px"><div class="mod-label"><span>Vectorpro certificate</span><span>10%</span></div><div class="mod-bar"><i></i></div></div>
    <div class="mod" style="left:296px;top:479px"><div class="mod-label"><span>Excellent knowledge</span><span>50%</span></div><div class="mod-bar"><i></i></div></div>
    <div class="mod" style="left:296px;top:515px"><div class="mod-label"><span>Interest</span><span>30%</span></div><div class="mod-bar"><i></i></div></div>

    <div class="panel" style="left:66px;top:608px;width:414px;height:334px"></div>
    <h2 class="sec-title center" style="top:632px">TRENDS PANE -- FREQUENCY<br><span class="accent">VS TIMELINE PLOT</span></h2>
    <svg class="abs" style="left:0;top:670px" width="546" height="230" viewBox="0 670 546 230" role="img" aria-label="Stacked bar chart of skill frequency per quarter">
      <line x1="119" y1="680" x2="119" y2="878" stroke="#c9c7d6" stroke-width=".8"/>
      <line x1="119" y1="878" x2="486" y2="878" stroke="#c9c7d6" stroke-width=".8"/>
      <g font-size="4.6" fill="#333" text-anchor="end">
        <text x="109" y="682">300</text><text x="109" y="696">280</text><text x="109" y="710">260</text><text x="109" y="724">240</text><text x="109" y="738">220</text><text x="109" y="752">200</text><text x="109" y="767">180</text><text x="109" y="781">160</text><text x="109" y="795">140</text><text x="109" y="809">120</text><text x="109" y="823">100</text><text x="109" y="837">80</text><text x="109" y="851">60</text><text x="109" y="866">40</text><text x="109" y="880">20</text>
      </g>
      <g>
        <rect x="131" y="686" width="26" height="63" fill="var(--sky)"/><rect x="131" y="749" width="26" height="79" fill="var(--magenta)"/><rect x="131" y="828" width="26" height="45" fill="var(--navy)"/>
        <rect x="178" y="774" width="26" height="33" fill="var(--sky)"/><rect x="178" y="807" width="26" height="47" fill="var(--magenta)"/><rect x="178" y="854" width="26" height="19" fill="var(--navy)"/>
        <rect x="225" y="719" width="26" height="30" fill="var(--sky)"/><rect x="225" y="749" width="26" height="79" fill="var(--magenta)"/><rect x="225" y="828" width="26" height="45" fill="var(--navy)"/>
        <rect x="271" y="705" width="26" height="44" fill="var(--sky)"/><rect x="271" y="749" width="26" height="105" fill="var(--magenta)"/><rect x="271" y="854" width="26" height="19" fill="var(--navy)"/>
        <rect x="318" y="774" width="26" height="33" fill="var(--sky)"/><rect x="318" y="807" width="26" height="47" fill="var(--magenta)"/><rect x="318" y="854" width="26" height="19" fill="var(--navy)"/>
        <rect x="365" y="686" width="26" height="63" fill="var(--sky)"/><rect x="365" y="749" width="26" height="79" fill="var(--magenta)"/><rect x="365" y="828" width="26" height="45" fill="var(--navy)"/>
        <rect x="412" y="774" width="26" height="33" fill="var(--sky)"/><rect x="412" y="807" width="26" height="47" fill="var(--magenta)"/><rect x="412" y="854" width="26" height="19" fill="var(--navy)"/>
        <rect x="458" y="686" width="26" height="63" fill="var(--sky)"/><rect x="458" y="749" width="26" height="79" fill="var(--magenta)"/><rect x="458" y="828" width="26" height="45" fill="var(--navy)"/>
      </g>
      <g font-size="5" fill="#fff" text-anchor="middle">
        <text x="144" y="722">290</text><text x="144" y="804">200</text><text x="144" y="857">80</text>
        <text x="191" y="796">150</text><text x="191" y="832">120</text><text x="191" y="867">20</text>
        <text x="238" y="737">240</text><text x="238" y="804">160</text><text x="238" y="857">80</text>
        <text x="284" y="726">240</text><text x="284" y="804">180</text><text x="284" y="869">20</text>
        <text x="331" y="796">150</text><text x="331" y="832">120</text><text x="331" y="867">20</text>
        <text x="378" y="722">290</text><text x="378" y="804">200</text><text x="378" y="857">80</text>
        <text x="425" y="796">150</text><text x="425" y="832">120</text><text x="425" y="867">20</text>
        <text x="471" y="722">290</text><text x="471" y="804">200</text><text x="471" y="857">80</text>
      </g>
      <g font-size="4.6" fill="#333" text-anchor="middle">
        <text x="134" y="893">2021 Q1</text><text x="183" y="893">2020 Q3</text><text x="232" y="893">2020 Q3</text><text x="280" y="893">2020 Q2</text><text x="330" y="893">2020 Q1</text><text x="378" y="893">2019 Q4</text><text x="427" y="893">2019 Q3</text><text x="476" y="893">2019 Q2</text>
      </g>
    </svg>

    <h2 class="sec-title" style="left:66px;top:975px">LEXICAL <span class="accent">INFORMATION</span></h2>
    <div class="mod-head" style="left:65px;top:1016px;font-size:9.5px">Synonymous expressions</div>
    <ul class="syn-list">
      <li><span class="tick"><svg width="5" height="4" viewBox="0 0 5 4"><path d="M.6 2 L2 3.3 L4.4 .7" stroke="#fff" stroke-width=".9" fill="none"/></svg></span>graphic designs</li>
      <li><span class="tick"><svg width="5" height="4" viewBox="0 0 5 4"><path d="M.6 2 L2 3.3 L4.4 .7" stroke="#fff" stroke-width=".9" fill="none"/></svg></span>visual design</li>
      <li><span class="tick"><svg width="5" height="4" viewBox="0 0 5 4"><path d="M.6 2 L2 3.3 L4.4 .7" stroke="#fff" stroke-width=".9" fill="none"/></svg></span>graphic designing</li>
    </ul>
    <div class="quote-banner">
      <div class="hero-bg" role="img" aria-label="Dark blue technology artwork behind a design quote" style="background:linear-gradient(110deg,#0c0a52 0%,#1d1a8e 45%,#2a2470 70%,#0e0b45 100%)"></div>
      <div class="quote-strip">A LOVE FOR CLEAN &amp; MINIMALISTIC<br>DESIGN</div>
    </div>

    <footer class="footer">
      <div class="mail"><span class="mail-icon"><svg width="11" height="8" viewBox="0 0 11 8"><rect x=".5" y=".5" width="10" height="7" rx="1" fill="#fff"/><path d="M1 1 L5.5 4.5 L10 1" stroke="#1c1b1f" fill="none"/></svg></span>Email : info@talentora.example</div>
      <div class="legal">© 2021 Talentora. All rights reserved &nbsp;| Privacy Policy &nbsp;| &nbsp;Terms of Use</div>
      <span class="social" style="left:429px"></span><span class="social" style="left:457px"></span>
    </footer>
  </section>

  <!-- SKILL TRENDS -->
  <section class="page page-trends">
    <header class="hero">
      <div class="hero-bg" role="img" aria-label="Dark navy financial candlestick chart artwork with a rising trend line" style="background:linear-gradient(180deg,#17105f 0%,#120c5a 60%,#0f0a52 100%)"></div>
      <div class="brand">Talentora</div>
      <nav class="nav"><span>HOME</span><span>EARLY CAREER</span><span class="active">SKILL TRENDS</span><span>SKILLS</span><span class="login">LOGIN</span></nav>
      <h1 class="hero-title">SKILL TRENDS</h1>
      <div class="crumbs">Home / Skill / Occupation / <em>Category</em></div>
    </header>

    <div class="banner">
      <div class="banner-photo" role="img" aria-label="Photo of a teacher writing notes at a desk" style="width:360px;background:linear-gradient(90deg,#c9c1ba 0%,#e6ddd6 30%,#f2f1ef 55%,#e9ebee 100%)"></div>
      <div class="banner-tag large" style="left:225px">Category<br>Teaching</div>
    </div>

    <h2 class="sec-title center" style="top:348px">OCCUPATION <span class="accent">CATEGORIES</span></h2>

    <svg class="abs" style="left:38px;top:420px" width="14" height="28" viewBox="0 0 14 28" aria-hidden="true"><path d="M12 1 L2 14 L12 27" stroke="#cfcfd6" stroke-width="1.2" fill="none"/></svg>
    <svg class="abs" style="left:494px;top:420px" width="14" height="28" viewBox="0 0 14 28" aria-hidden="true"><path d="M2 1 L12 14 L2 27" stroke="#cfcfd6" stroke-width="1.2" fill="none"/></svg>

    <div class="cat" style="left:101px"><div class="cat-ring"><svg width="26" height="26" viewBox="0 0 26 26" fill="none" stroke="var(--magenta)" stroke-width="1.3"><rect x="3" y="7" width="20" height="16"/><path d="M1 7 L13 2 L25 7"/><path d="M7 11v8M11 11v8M15 11v8M19 11v8"/></svg></div><div class="cat-name">Armed Forces</div></div>
    <div class="cat" style="left:187px"><div class="cat-ring"><svg width="26" height="26" viewBox="0 0 26 26" fill="none" stroke="var(--magenta)" stroke-width="1.3"><circle cx="13" cy="10" r="6"/><circle cx="13" cy="10" r="2.5"/><path d="M4 24c1-5 4-7 9-7s8 2 9 7"/></svg></div><div class="cat-name">Managers</div></div>
    <div class="cat" style="left:273px"><div class="cat-ring active"><svg width="26" height="26" viewBox="0 0 26 26" fill="none" stroke="var(--navy)" stroke-width="1.3"><circle cx="13" cy="8" r="5"/><path d="M4 24c1-6 4-9 9-9s8 3 9 9"/><path d="M13 15v9"/></svg></div><div class="cat-name">Professionals</div><div class="cat-sub">Science and engineering<br>Health Teaching<br>Business and administration<br>Information and communication<br>Legal, social and cultura</div></div>
    <div class="cat" style="left:359px"><div class="cat-ring"><svg width="26" height="26" viewBox="0 0 26 26" fill="none" stroke="var(--magenta)" stroke-width="1.3"><rect x="2" y="4" width="16" height="11" rx="1"/><path d="M7 19h6M10 15v4"/><circle cx="20" cy="16" r="4"/></svg></div><div class="cat-name">Technicians and<br>associate<br>professionals</div></div>
    <div class="cat" style="left:445px"><div class="cat-ring"><svg width="26" height="26" viewBox="0 0 26 26" fill="none" stroke="var(--magenta)" stroke-width="1.3"><circle cx="13" cy="9" r="5"/><path d="M7 9a6 6 0 0 1 12 0"/><path d="M5 24c1-5 4-8 8-8s7 3 8 8"/></svg></div><div class="cat-name">Clerical<br>support</div></div>

    <h2 class="sec-title" style="left:138px;top:590px;width:240px;text-align:center">TIME EVOLUTION OF SKILLS<br><span class="accent">IN THIS CATEGORY</span></h2>
    <svg class="abs" style="left:0;top:575px" width="546" height="230" viewBox="0 575 546 230" role="img" aria-label="Line chart of skill evolution over time for ICT and overall">
      <line x1="113" y1="600" x2="113" y2="783" stroke="#d5d5dc" stroke-width=".8"/>
      <line x1="113" y1="783" x2="480" y2="783" stroke="#d5d5dc" stroke-width=".8"/>
      <g font-size="4.6" fill="#333" text-anchor="end">
        <text x="100" y="617">Time</text><text x="100" y="654">Project Management Skills</text><text x="100" y="691">Use of Office Software</text><text x="100" y="728">Innovative teaching Techniques</text><text x="100" y="765">Pedagogy</text>
      </g>
      <polyline points="138,726 197,737 250,715 302,675 356,683 410,667" fill="none" stroke="var(--magenta)" stroke-width="1.6"/>
      <polyline points="144,773 198,753 252,741 304,711 358,655 412,587" fill="none" stroke="var(--navy)" stroke-width="1.6"/>
      <g fill="var(--magenta)"><circle cx="138" cy="726" r="3"/><circle cx="197" cy="737" r="3"/><circle cx="250" cy="715" r="3"/><circle cx="302" cy="675" r="3"/><circle cx="356" cy="683" r="3"/><circle cx="410" cy="667" r="3"/></g>
      <g fill="var(--navy)"><rect x="141" y="770" width="6" height="6"/><rect x="195" y="750" width="6" height="6"/><rect x="249" y="738" width="6" height="6"/><rect x="301" y="708" width="6" height="6"/><rect x="355" y="652" width="6" height="6"/><rect x="409" y="584" width="6" height="6"/></g>
      <rect x="421" y="688" width="6" height="6" fill="var(--magenta)"/><text x="433" y="694" font-size="5" fill="#333">ICT</text>
      <rect x="421" y="700" width="6" height="6" fill="var(--navy)"/><text x="433" y="706" font-size="5" fill="#333">OVERALL</text>
      <g font-size="4.6" fill="#333" text-anchor="middle">
        <text x="128" y="797">2021 Q1</text><text x="177" y="797">2020 Q3</text><text x="225" y="797">2020 Q3</text><text x="274" y="797">2020 Q2</text><text x="323" y="797">2020 Q1</text><text x="372" y="797">2019 Q4</text><text x="420" y="797">2019 Q3</text><text x="470" y="797">2019 Q2</text>
      </g>
    </svg>

    <h3 class="sec-title small" style="left:65px;top:840px;font-size:10.5px;line-height:12px">LIST OF TRENDING<br><span class="accent">SKILLS</span></h3>
    <h3 class="sec-title small" style="left:207px;top:840px;font-size:10.5px;line-height:12px">LIST OF EMERGING<br><span class="accent">SKILLS</span></h3>
    <h3 class="sec-title small" style="left:349px;top:840px;font-size:10.5px;line-height:12px">LIST OF TRANSFERRING<br><span class="accent">SKILLS</span></h3>

    <table class="data-table mini" style="left:65px;top:876px;width:131px">
      <thead><tr><th style="width:100px">SKILL</th><th>SCORE</th></tr></thead>
      <tbody>
        <tr><td>Alternative Teaching Techniques</td><td class="score">0.97</td></tr>
        <tr><td>Use of Course Management Software</td><td class="score">0.89</td></tr>
        <tr><td>Use of Electronic Records Systems</td><td class="score">0.41</td></tr>
        <tr><td>Education of children with special needs</td><td class="score">0.31</td></tr>
      </tbody>
    </table>
    <table class="data-table mini" style="left:207px;top:876px;width:131px">
      <thead><tr><th style="width:100px">SKILL</th><th>SCORE</th></tr></thead>
      <tbody>
        <tr><td>Video editing</td><td class="score">0.97</td></tr>
        <tr><td>Organization of Online Events</td><td class="score">0.89</td></tr>
        <tr><td>Use of Electronic Records Systems</td><td class="score">0.41</td></tr>
        <tr><td>Use of Electronic Records Systems</td><td class="score">0.31</td></tr>
      </tbody>
    </table>
    <table class="data-table mini" style="left:349px;top:876px;width:131px">
      <thead><tr><th style="width:100px">SKILL</th><th>SCORE</th></tr></thead>
      <tbody>
        <tr><td>Video editing</td><td class="score">0.97</td></tr>
        <tr><td>Organization of Online Events</td><td class="score">0.89</td></tr>
        <tr><td>Use of Electronic Records Systems</td><td class="score">0.41</td></tr>
        <tr><td>Development of educational software</td><td class="score">0.31</td></tr>
      </tbody>
    </table>

    <footer class="footer">
      <div class="mail"><span class="mail-icon"><svg width="11" height="8" viewBox="0 0 11 8"><rect x=".5" y=".5" width="10" height="7" rx="1" fill="#fff"/><path d="M1 1 L5.5 4.5 L10 1" stroke="#1c1b1f" fill="none"/></svg></span>Email : info@talentora.example</div>
      <div class="legal">© 2021 Talentora. All rights reserved &nbsp;| Privacy Policy &nbsp;| &nbsp;Terms of Use</div>
      <span class="social" style="left:429px"></span><span class="social" style="left:457px"></span>
    </footer>
  </section>
</div>
</body>
</html>
```